Webdesign für Steuerberaterin
Zielgruppe
Ich bin Steuerberaterin. Meine Zielgruppe sind sowohl Privatpersonen als auch Unternehmer sowie Männer und Frauen.
Aufgabenstellung
Bitte mein Logo und Foto mit berücksichtigen. Ich möchte keine Website, auf der alle 'Reiter' als eine Seite von oben nach unten durchlaufen. Sondern wirklich einzelne, voneinander getrennte Seiten.

```html
<!DOCTYPE html>
<html lang="de">
<head>
<meta charset="utf-8">
<title>Maren Brodtke – Über mich</title>
<link rel="stylesheet" href="https://fonts.googleapis.com/css2?family=Fira+Sans:wght@400;600;700;800&family=Tinos&display=swap">
<style>
  :root {
    --sidebar: #1e252c;
    --gold: #b08a2e;
    --gold-bright: #dbb93d;
    --rule: #c9a43a;
    --text: #4a4a4a;
    --title: #3f3f3f;
    --line: #2a1d16;
    --white: #ffffff;
    --box-border: #d2d2d2;
  }
  * { margin: 0; padding: 0; box-sizing: border-box; }
  html, body { width: 1200px; height: 768px; overflow: hidden; background: var(--white); }
  body { position: relative; font-family: "Fira Sans", Arial, sans-serif; color: var(--text); }

  .sidebar { position: absolute; left: 0; top: 0; width: 308px; height: 742px; background: var(--sidebar); }
  .nav { position: absolute; left: 80px; top: 0; list-style: none; }
  .nav li { position: absolute; left: 0; white-space: nowrap; font-size: 12.5px; line-height: 18px; }
  .nav a { color: var(--gold); text-decoration: none; }
  .nav .current a { color: var(--white); }
  .paragraph-mark { position: absolute; left: 37px; top: 419px; width: 142px; height: 290px;
    background: linear-gradient(180deg, #8f8879 0%, #d9d5c8 35%, #f2f0e8 55%, #c7c1b2 80%, #7e776a 100%);
    border-radius: 70px; }

  .brand { position: absolute; left: 372px; top: 66px; width: 140px; text-align: center; }
  .brand-dot { display: block; width: 14px; height: 14px; border-radius: 50%; background: var(--gold); margin: 0 auto 10px; }
  .brand-name { font-size: 16px; font-weight: 400; color: var(--gold); white-space: nowrap; }

  .portrait { position: absolute; left: 270px; top: 186px; width: 221px; height: 349px;
    background: linear-gradient(180deg, #eceef3 0%, #e3e5ec 45%, #2a2f3c 62%, #1f2430 100%); }

  .section-title { position: absolute; font-family: "Tinos", "Times New Roman", serif; font-weight: 400;
    color: var(--gold); font-size: 24px; line-height: 30px; transform: translateX(-50%); white-space: nowrap; }
  .about-title { left: 934px; top: 138px; }
  .about-rule { position: absolute; left: 693px; top: 187px; width: 475px; height: 2px; background: var(--rule); }
  .intro { position: absolute; left: 690px; top: 232px; width: 474px; text-align: center;
    font-size: 13.4px; line-height: 20.4px; color: var(--text); }
  .intro strong { font-weight: 800; color: var(--title); }
  .career-title { left: 941px; top: 414px; }

  .timeline-axis { position: absolute; left: 941px; top: 455px; width: 2px; height: 263px; background: var(--line); }
  .milestone { position: absolute; width: 178px; height: 50px; background: var(--white);
    border: 1px solid var(--box-border); box-shadow: 1px 2px 2px rgba(0,0,0,0.25); padding: 7px 12px; }
  .milestone .year { display: block; font-size: 10.8px; line-height: 13px; font-weight: 600; color: var(--gold-bright); }
  .milestone .role { display: block; font-size: 14.8px; line-height: 18px; font-weight: 700; color: var(--title); margin-top: 1px; white-space: nowrap; }
  .connector { position: absolute; height: 2px; width: 18px; background: var(--line); }
  .node { position: absolute; width: 10px; height: 10px; border-radius: 50%; background: var(--gold-bright);
    border: 2px solid var(--line); }

  .footer { position: absolute; left: 0; top: 742px; width: 1200px; height: 26px; background: var(--gold-bright);
    padding-left: 81px; font-size: 12px; line-height: 26px; color: var(--sidebar); }
  .footer span { margin: 0 8px; }
</style>
</head>
<body>
  <aside class="sidebar">
    <ul class="nav">
      <li class="current" style="top:185px"><a href="#">Über mich</a></li>
      <li style="top:252px"><a href="#">Leistungen</a></li>
      <li style="top:323px"><a href="#">Kontakt</a></li>
    </ul>
    <div class="paragraph-mark" role="img" aria-label="Großes Paragrafenzeichen als Dekoration"></div>
  </aside>

  <div class="brand">
    <span class="brand-dot"></span>
    <span class="brand-name">Maren Brodtke</span>
  </div>

  <div class="portrait" role="img" aria-label="Porträtfoto der Steuerberaterin im dunklen Blazer"></div>

  <h1 class="section-title about-title">Über mich</h1>
  <div class="about-rule"></div>
  <p class="intro">
    <strong>Ich bin Maren Brodtke, Steuerberaterin aus Leidenschaft,</strong><br>
    und wohne mit meinem Mann und meinem Sohn in Haselbrook.<br>
    Ich habe meinen Beruf „von der Pike auf“ gelernt<br>
    und möchte Sie gerne kompetent und zuverlässig<br>
    in Ihrem beruflichen Alltag begleiten und Ihnen „den Rücken freihalten“,<br>
    so dass Sie sich voll und ganz auf Ihr Kerngeschäft konzentrieren können.
  </p>

  <h2 class="section-title career-title">Werdegang</h2>
  <div class="timeline-axis"></div>

  <div class="milestone" style="left:746px; top:497px"><span class="year">2004</span><span class="role">Abitur</span></div>
  <div class="connector" style="left:925px; top:520px"></div>
  <div class="node" style="left:936px; top:516px"></div>

  <div class="milestone" style="left:960px; top:542px"><span class="year">seit 2008</span><span class="role">Steuerfachangestellte</span></div>
  <div class="connector" style="left:943px; top:565px"></div>
  <div class="node" style="left:936px; top:561px"></div>

  <div class="milestone" style="left:746px; top:587px"><span class="year">seit 2012</span><span class="role">Steuerfachwirtin</span></div>
  <div class="connector" style="left:925px; top:610px"></div>
  <div class="node" style="left:936px; top:606px"></div>

  <div class="milestone" style="left:960px; top:627px"><span class="year">seit 2018</span><span class="role">Steuerberaterin</span></div>
  <div class="connector" style="left:943px; top:650px"></div>
  <div class="node" style="left:936px; top:646px"></div>

  <footer class="footer">Impressum<span>|</span>Datenschutz</footer>
</body>
</html>
```